Business Cards - Brightpath Horizon

need to design unique business card for my mortgage business. I need to design credit card style business card for my business or any unique idea that you might have

Target Market(s)

Home Loan customers

Industry/Entity Type

Mortgage Brokerage

Contact Information for Business Card

please design credit card style or very unique style business card

Colors

Designer to choose colors to be used in the design.

Requirements
Must have
• Name
• position
• Phone number
• fax number
• email address
• website address
• social media address
• All above fields will be provided once design in finalised

```html
<!DOCTYPE html>
<html lang="en">
<head>
<meta charset="utf-8">
<title>Brightpath Horizon – Business Card</title>
<link rel="stylesheet" href="https://fonts.googleapis.com/css2?family=Libre+Baskerville:wght@400;700&family=Share+Tech+Mono&display=swap">
<style>
  :root {
    --page-bg: #e9e6e1;
    --card-light: #4fb0ea;
    --card-mid: #2a8bd6;
    --card-deep: #155fae;
    --ink-white: #f4f8fc;
    --ink-soft: #d8e6f2;
    --brand-navy: #1b2a6b;
    --social-fill: #c9a86a;
  }
  html, body {
    margin: 0;
    padding: 0;
    width: 1200px;
    height: 969px;
    overflow: hidden;
    background: var(--page-bg);
  }
  .card {
    position: absolute;
    left: 100px;
    top: 201px;
    width: 1000px;
    height: 567px;
    border-radius: 30px;
    overflow: hidden;
    background:
      radial-gradient(ellipse 40% 55% at 72% 62%, rgba(10,50,110,0.35), transparent 70%),
      radial-gradient(ellipse 45% 60% at 18% 30%, rgba(140,210,250,0.35), transparent 70%),
      linear-gradient(100deg, var(--card-light) 0%, var(--card-mid) 50%, var(--card-deep) 100%);
    box-shadow: 0 10px 30px rgba(0,0,0,0.18);
    font-family: "Libre Baskerville", Georgia, serif;
  }
  .holder { position: absolute; left: 46px; top: 70px; }
  .holder-name {
    margin: 0;
    font-size: 26px;
    font-weight: 700;
    color: var(--ink-white);
    letter-spacing: 0.5px;
  }
  .holder-title {
    margin: 10px 0 0;
    font-size: 21px;
    font-weight: 700;
    color: var(--ink-white);
    letter-spacing: 0.5px;
  }
  .brand {
    position: absolute;
    right: 52px;
    top: 52px;
    text-align: right;
    font-size: 36px;
    font-weight: 700;
    line-height: 1.15;
    color: var(--brand-navy);
    margin: 0;
  }
  .card-number {
    position: absolute;
    left: 0;
    right: 0;
    top: 244px;
    text-align: center;
    font-family: "Share Tech Mono", "Courier New", monospace;
    font-size: 60px;
    line-height: 72px;
    letter-spacing: 6px;
    word-spacing: 22px;
    color: var(--ink-white);
    margin: 0;
  }
  .contact {
    position: absolute;
    left: 46px;
    top: 440px;
    margin: 0;
    padding: 0;
    list-style: none;
    font-size: 21px;
    line-height: 32px;
    color: var(--ink-soft);
  }
  .social {
    position: absolute;
    left: 718px;
    top: 478px;
  }
</style>
</head>
<body>
  <div class="card">
    <div class="holder">
      <p class="holder-name">DANIEL HART</p>
      <p class="holder-title">CEO/FOUNDER</p>
    </div>

    <p class="brand">Brightpath<br>Horizon</p>

    <p class="card-number">730 415 2968</p>

    <ul class="contact">
      <li>P. 555 214 7730</li>
      <li>mail@brightpath.com</li>
      <li>www.brightpath.com</li>
    </ul>

    <svg class="social" width="240" height="52" viewBox="0 0 240 52" role="img" aria-label="Social media profile links">
      <circle cx="27" cy="26" r="25" fill="var(--social-fill)"/>
      <circle cx="87" cy="26" r="25" fill="var(--social-fill)"/>
      <circle cx="147" cy="26" r="25" fill="var(--social-fill)"/>
      <circle cx="207" cy="26" r="25" fill="var(--social-fill)"/>
    </svg>
  </div>
</body>
</html>
```